New Business Cards for Tormin Group

We need a new Business Card to compliment our new logo. We are a vibrant design, manufacture and install business providing recreation areas, public parks and Municipal spaces. We want business cards that are classy, modern and clean.

We have recently changed our logo, and are celebrating our 40th anniversary. We want business cards with a new modern design to reflect our status.

Target Market(s)

Customers

Contact Information for Business Card

We need all the details of our 3 offices as per the business card attached. Please disregard the old logo on the business card, the other three files show our new logo.

Requirements
Must have
• All info as per attached business card but with new logo.
Nice to have

```html
<!DOCTYPE html>
<html lang="en">
<head>
<meta charset="utf-8">
<title>Tormin Group – Business Card</title>
<link href="https://fonts.googleapis.com/css2?family=Lato:wght@400;700&family=Roboto:wght@400;500;700&display=swap" rel="stylesheet">
<style>
  :root {
    --red: #e8323a;
    --charcoal: #48484c;
    --ink: #3b3b3f;
    --paper: #ffffff;
    --backdrop: #ece9e4;
  }
  * { margin: 0; padding: 0; box-sizing: border-box; }
  html, body { width: 1200px; height: 900px; overflow: hidden; }
  body {
    background: var(--backdrop);
    font-family: "Roboto", Arial, sans-serif;
    color: var(--ink);
    position: relative;
  }
  .card {
    position: absolute;
    width: 570px;
    height: 352px;
    box-shadow: 2px 3px 6px rgba(0,0,0,0.25);
    overflow: hidden;
  }
  .card-front { left: 330px; top: 71px; background: var(--paper); }
  .card-back { left: 331px; top: 462px; width: 572px; height: 350px; background: var(--charcoal); }

  .person { position: absolute; left: 21px; top: 27px; }
  .person-name {
    font-family: "Lato", Arial, sans-serif;
    font-weight: 700; font-size: 21px; color: var(--red); letter-spacing: 0.2px;
  }
  .person-role { font-size: 14px; margin-top: 2px; }
  .person-contact { margin-top: 8px; }

  .line { font-size: 14px; line-height: 18px; white-space: nowrap; }
  .line .label { color: var(--red); font-weight: 700; }

  .office { position: absolute; }
  .office-title { font-size: 18px; font-weight: 500; color: var(--red); margin-bottom: 4px; }
  .office-head { left: 21px; top: 128px; }
  .office-dubai { left: 21px; top: 230px; }
  .office-qatar { left: 271px; top: 229px; }

  .front-band { position: absolute; left: 0; bottom: 0; width: 100%; height: 20px; }

  .brand { position: absolute; display: flex; align-items: center; gap: 12px; }
  .brand-dot { border-radius: 50%; background: var(--red); flex: none; }
  .brand-name {
    font-family: "Roboto", Arial, sans-serif; font-weight: 700;
    line-height: 1; letter-spacing: 1px; white-space: nowrap;
  }
  .brand-name span { display: block; }
  .brand-front { left: 296px; top: 89px; }
  .brand-front .brand-dot { width: 70px; height: 70px; }
  .brand-front .brand-name { font-size: 32px; color: var(--ink); }
  .brand-back { left: 111px; top: 88px; gap: 18px; }
  .brand-back .brand-dot { width: 120px; height: 120px; }
  .brand-back .brand-name { font-size: 52px; color: var(--paper); }

  .back-band {
    position: absolute; left: 0; bottom: 0; width: 100%; height: 47px;
    background: var(--red); color: var(--paper);
    display: flex; align-items: center; justify-content: center;
    font-size: 18px;
  }
</style>
</head>
<body>

<section class="card card-front">
  <div class="person">
    <div class="person-name">MAREK LINDQVIST</div>
    <div class="person-role">Managing Partner</div>
    <div class="person-contact">
      <div class="line"><span class="label">M:</span> +971 (0)50 555 0147</div>
      <div class="line"><span class="label">E:</span> marek@tormingroup.com</div>
    </div>
  </div>

  <div class="office office-head">
    <div class="office-title">Head Office</div>
    <div class="line">P.O.Box:31840 Abu Dhabi,U.A.E.</div>
    <div class="line"><span class="label">P :</span> +971 (0)2 5550184</div>
    <div class="line"><span class="label">F :</span> +971 (0)2 5550185</div>
    <div class="line"><span class="label">E :</span> sales@tormingroup.com</div>
  </div>

  <div class="office office-dubai">
    <div class="office-title">Dubai Office</div>
    <div class="line">P.O.Box:402716 Dubai,U.A.E.</div>
    <div class="line"><span class="label">P :</span> +971 (0)4 5550291</div>
    <div class="line"><span class="label">F :</span> +971 (0)2 5550292</div>
    <div class="line"><span class="label">E :</span> sales@tormingroup.com</div>
  </div>

  <div class="office office-qatar">
    <div class="office-title">Qatar Office</div>
    <div class="line">P.O.Box:18273 Doha, Qatar</div>
    <div class="line"><span class="label">P :</span> +974 55501930</div>
    <div class="line"><span class="label">F :</span> +974 55501931</div>
    <div class="line"><span class="label">E :</span> sales@tormingroup.com</div>
  </div>

  <div class="brand brand-front">
    <span class="brand-dot"></span>
    <span class="brand-name"><span>TORMIN</span><span>GROUP</span></span>
  </div>

  <svg class="front-band" viewBox="0 0 570 20" preserveAspectRatio="none" aria-hidden="true">
    <polygon points="0,8 242,8 238,20 0,20" fill="var(--charcoal)"/>
    <polygon points="244,0 570,0 570,20 238,20" fill="var(--red)"/>
  </svg>
</section>

<section class="card card-back">
  <div class="brand brand-back">
    <span class="brand-dot"></span>
    <span class="brand-name"><span>TORMIN</span><span>GROUP</span></span>
  </div>
  <div class="back-band">www.tormingroup.com</div>
</section>

</body>
</html>
```